Veltrona Pocket Folder

Create a new pocket folder
An Overview / Background of the Business & Services
We would like a new folder to use when making formal presentations
* The Target Market / Audience you are trying to reach
The target audience are commercial businesses that we are selling group insurance products to
* Design Specifics; any preferences or ideas for Style, Colour, Imagery, etc
We wanted to use the Houston, Texas skyline and create something that was simple, yet modern.
* Do you have an existing website or Facebook page were designers can learn more about your company?
Yes, http://www.veltronagroup.example and we are on Linked-In.
Updates
Project Deadline Extended Reason: We have many people who have to agree. We need to get an answer on the form of the ready art we will receive when we select a designer .Thank you. Added Thursday, April 27, 2017
Industry/Entity Type
Business
Look and feel
Each slider illustrates characteristics of the customer's brand and the style your logo design should communicate.

```html
<!DOCTYPE html>
<html lang="en">
<head>
<meta charset="utf-8">
<title>Veltrona Pocket Folder</title>
<link href="https://fonts.googleapis.com/css2?family=Roboto:wght@700&family=Open+Sans:wght@400;700&display=swap" rel="stylesheet">
<style>
  :root {
    --backdrop: #e8e8e8;
    --paper: #ffffff;
    --slate: #6d6e71;
    --slate-dark: #5b5c5f;
    --tab-text: #c9cacc;
    --brand-blue: #1b8fd3;
    --blue-light: #22a3dd;
    --blue-deep: #0f7cc4;
    --skyline-grey: #d3d4d6;
    --skyline-blue: #dde7ef;
    --ghost: #eef2f5;
  }
  html, body {
    margin: 0;
    padding: 0;
    width: 1200px;
    height: 979px;
    overflow: hidden;
    background: var(--backdrop);
  }
  body { position: relative; }
  .folder-dieline {
    display: block;
    width: 1200px;
    height: 979px;
  }
  .side-tab { fill: var(--slate); }
  .tab-url {
    font-family: "Open Sans", sans-serif;
    font-size: 7.5px;
    letter-spacing: 1.6px;
    fill: var(--tab-text);
  }
  .cover-panel { fill: url(#paperShade); }
  .fold-line { stroke: #ececec; stroke-width: 1; }
  .ghost-mark { fill: var(--ghost); }
  .brand-square { fill: var(--brand-blue); }
  .brand-name {
    font-family: "Roboto", sans-serif;
    font-weight: 700;
    font-size: 40px;
    fill: var(--slate-dark);
  }
  .wave-band { fill: var(--slate); }
  .wave-edge { fill: none; stroke: var(--paper); stroke-width: 2.5; }
  .wave-body { fill: url(#blueGlow); }
  .pocket { fill: url(#pocketGlow); }
  .card-slit { stroke: var(--paper); stroke-width: 1.2; }

  .contact-block {
    position: absolute;
    left: 219px;
    top: 614px;
    font-family: "Open Sans", sans-serif;
    font-size: 7.7px;
    line-height: 12px;
    color: var(--paper);
    white-space: nowrap;
  }
  .contact-row {
    display: flex;
    align-items: center;
    gap: 3px;
    padding-left: 6px;
  }
  .contact-item {
    display: inline-flex;
    align-items: center;
    gap: 2px;
    margin-right: 3px;
  }
  .contact-icon {
    width: 7px;
    height: 7px;
    fill: var(--paper);
    flex: none;
  }
  .contact-address .company { font-weight: 700; }
</style>
</head>
<body>
<svg class="folder-dieline" viewBox="0 0 1177 960" xmlns="http://www.w3.org/2000/svg">
  <defs>
    <linearGradient id="paperShade" x1="0" y1="0" x2="1" y2="0">
      <stop offset="0" stop-color="#ffffff"/>
      <stop offset="0.5" stop-color="#f7f7f7"/>
      <stop offset="1" stop-color="#f1f1f1"/>
    </linearGradient>
    <radialGradient id="blueGlow" cx="0.45" cy="0.7" r="0.7">
      <stop offset="0" stop-color="var(--blue-light)"/>
      <stop offset="1" stop-color="var(--blue-deep)"/>
    </radialGradient>
    <radialGradient id="pocketGlow" cx="0.5" cy="0.45" r="0.65">
      <stop offset="0" stop-color="var(--blue-light)"/>
      <stop offset="1" stop-color="var(--blue-deep)"/>
    </radialGradient>
    <linearGradient id="skylineTone" x1="0" y1="0" x2="1" y2="0">
      <stop offset="0" stop-color="var(--skyline-grey)"/>
      <stop offset="0.5" stop-color="var(--skyline-blue)"/>
      <stop offset="1" stop-color="var(--skyline-grey)"/>
    </linearGradient>
  </defs>

  <path class="side-tab" d="M100,115 H137 V665 H100 V472 A12,12 0 0 0 100,448 Z"/>
  <path class="side-tab" d="M1015,115 H1052 V448 A12,12 0 0 0 1052,472 V665 H1015 Z"/>
  <text class="tab-url" transform="translate(122,350) rotate(-90)">www.veltronagroup.example</text>
  <text class="tab-url" transform="translate(1037,350) rotate(-90)">www.veltronagroup.example</text>

  <path class="pocket" d="M166,668 H575 L546,840 Q541,872 520,872 H166 Z"/>
  <path class="pocket" d="M578,668 H985 V875 H628 Q608,875 605,850 Z"/>
  <g class="card-slots">
    <line class="card-slit" x1="711" y1="755" x2="740" y2="727"/>
    <line class="card-slit" x1="845" y1="727" x2="873" y2="755"/>
    <line class="card-slit" x1="711" y1="793" x2="740" y2="822"/>
    <line class="card-slit" x1="845" y1="822" x2="873" y2="793"/>
  </g>

  <rect class="cover-panel" x="136" y="115" width="880" height="553"/>
  <line class="fold-line" x1="575" y1="115" x2="575" y2="668"/>

  <rect class="ghost-mark" x="272" y="197" width="157" height="154" rx="20"/>

  <g class="brand-lockup">
    <rect class="brand-square" x="656" y="259" width="52" height="52" rx="6"/>
    <text class="brand-name" x="718" y="301">Veltrona</text>
  </g>

  <rect class="skyline" role="img" aria-label="Houston city skyline silhouette in soft grey and pale blue" x="160" y="400" width="856" height="220" fill="url(#skylineTone)"/>

  <path class="wave-band" d="M136,514 C190,480 290,484 410,520 S650,600 800,630 S960,628 1016,610 L1016,668 L136,668 Z"/>
  <path class="wave-body" d="M136,530 C190,496 290,500 410,536 S650,616 800,646 S960,644 1016,624 L1016,668 L136,668 Z"/>
  <path class="wave-edge" d="M136,527 C190,493 290,497 410,533 S650,613 800,643 S960,641 1016,621"/>
</svg>

<div class="contact-block">
  <div class="contact-row">
    <span class="contact-item">
      <svg class="contact-icon" viewBox="0 0 10 10"><path d="M1,1 q1,-1 2,0 l1.5,2 q-1,1 0,2 l1.5,1.5 q1,1 2,0 l2,1.5 q1,1 0,2 q-4,2 -8,-2 q-4,-4 -1,-7 Z"/></svg>
      <span>555-014-2290</span>
    </span>
    <span class="contact-item">
      <svg class="contact-icon" viewBox="0 0 10 10"><rect x="0" y="2" width="10" height="7"/></svg>
      <span>info@veltronagroup.example</span>
    </span>
    <span class="contact-item">
      <svg class="contact-icon" viewBox="0 0 10 10"><circle cx="5" cy="5" r="5"/></svg>
      <span>www.veltronagroup.example</span>
    </span>
  </div>
  <div class="contact-address"><span class="company">Veltrona Agency LLC,</span> 1200 Harbor Loop, Suite 400, Springfield, 00000</div>
</div>
</body>
</html>
```